UI/ UX Design for ERP Software

We need a new UX/UI interface for a ERP software for property managers. Our CMMS / ERP solution is made based on responsive design technologies and is coded in PHP.
The overall UX to be similar to Tev Ulna - easy navigation, intuitive menus.

Industry/Entity Type

Property Management

Number of Pages Required

5+ page

Requirements
Must have
• Round dock buttons
Consistent icons across the application
Enough Spacing between buttons/icons/ menu
Consistent Font
Nice to have
• We would like the UX to allow the users to use the application without /minimum training.
Should not have
• we don't want anything that is classic with respect to UX

```html
<!DOCTYPE html>
<html lang="en">
<head>
<meta charset="utf-8">
<title>Hearthly – Maintenance calendar</title>
<link href="https://fonts.googleapis.com/css2?family=Inter:wght@400;500;600;700&display=swap" rel="stylesheet">
<style>
  :root{
    --page:#f1f6fd;
    --window:#f3f8fe;
    --ink:#1b2430;
    --muted:#5d7a93;
    --panel:#e1eef8;
    --cell:#ffffff;
    --cell-line:#dfe9f2;
    --cell-past:#c8e3f4;
    --past-num:#6c8799;
    --blue:#1178e4;
    --blue-bright:#0d8ef5;
    --orange:#f2703f;
    --chip-line:#d5dde5;
    --sun:#f5b400;
  }
  *{box-sizing:border-box;margin:0;padding:0}
  html,body{width:1200px;height:1200px;overflow:hidden}
  body{background:var(--page);font-family:"Inter",sans-serif;color:var(--ink);position:relative}

  .app-window{position:absolute;left:188px;top:61px;width:826px;height:1077px;background:var(--window);border-radius:19px;box-shadow:0 10px 40px rgba(40,80,130,.08)}
  .window-dots{position:absolute;left:29px;top:14px;display:flex;gap:5px}
  .window-dots span{width:6px;height:6px;border-radius:50%}
  .dot-yellow{background:#f8c43a}.dot-red{background:#f04b4b}.dot-green{background:#35c759}

  .brand{position:absolute;left:25px;top:34px;display:flex;align-items:center;gap:5px;font-size:13px;font-weight:700;color:var(--blue)}
  .brand-mark{width:11px;height:11px;background:var(--blue);border-radius:2px}

  .user-bar{position:absolute;right:27px;top:27px;display:flex;align-items:center}
  .theme-toggle{width:50px;height:20px;border-radius:10px;background:#fff;border:1px solid #e6ecf2;display:flex;align-items:center;justify-content:space-between;padding:0 4px 0 5px;margin-right:13px}
  .theme-toggle .knob{width:13px;height:13px;border-radius:50%;border:2px solid var(--sun);background:#ffe27a}
  .welcome{font-size:9.5px;margin-right:11px}
  .welcome b{font-weight:600}
  .avatar{width:31px;height:31px;border-radius:50%;background:radial-gradient(circle at 50% 40%,#8a6a55,#3a2e2a 75%)}

  .section-title{position:absolute;left:29px;top:71px;display:flex;align-items:center;gap:6px;font-size:14px;font-weight:600}

  .property-tabs{position:absolute;left:29px;top:105px;display:flex;gap:4px}
  .property-tabs button{width:86px;height:26px;border:1px solid var(--chip-line);background:#f7fafd;border-radius:4px;font:500 7px "Inter",sans-serif;color:var(--ink)}

  .view-switch{position:absolute;left:29px;top:152px;display:flex;gap:10px}
  .view-switch button{height:31px;border:0;border-radius:4px;font:600 8.7px "Inter",sans-serif;display:flex;align-items:center;justify-content:center;gap:5px}
  .btn-requests{width:126px;background:#fff;color:var(--ink)}
  .btn-calendar{width:145px;background:var(--blue-bright);color:#fff;box-shadow:0 6px 14px rgba(13,142,245,.3)}

  .month-nav{position:absolute;right:28px;top:199px;display:flex;align-items:center}
  .month-nav h2{font-size:13.5px;font-weight:500;margin-right:22px;letter-spacing:.2px}
  .nav-btn{width:24px;height:23px;border-radius:3px;display:flex;align-items:center;justify-content:center}
  .nav-prev{background:#dfeaf3;margin-right:14px}
  .nav-next{background:#fff;box-shadow:0 2px 6px rgba(0,0,0,.08)}

  .calendar{position:absolute;left:25px;top:234px;width:773px;height:736px;background:var(--panel);border-radius:8px;padding:0 11px}
  .weekdays{display:grid;grid-template-columns:repeat(7,103px);column-gap:5px;height:35px;align-items:center;text-align:center;font-size:11px;color:var(--muted)}
  .days{display:grid;grid-template-columns:repeat(7,103px);grid-auto-rows:165px;gap:6px 5px}
  .day{background:var(--cell);border:1px solid var(--cell-line);position:relative;padding-top:30px}
  .day.past{background:var(--cell-past);border-color:var(--cell-past)}
  .day-num{position:absolute;top:10px;right:6px;font-size:9px;font-weight:600}
  .day.past .day-num{color:var(--past-num)}
  .event{height:26px;margin:0 -1px 10px;padding:4px 8px;color:#fff;font-size:7px;font-weight:600;line-height:10px}
  .event.blue{background:var(--blue)}
  .event.orange{background:var(--orange)}

  .dock{position:absolute;left:347px;top:998px;width:131px;height:52px;background:#fff;border-radius:9px;display:flex;align-items:center;justify-content:center;gap:28px;box-shadow:0 6px 20px rgba(40,80,130,.07)}
  .dock-btn{width:34px;height:34px;border-radius:8px;display:flex;align-items:center;justify-content:center}
  .dock-home{background:linear-gradient(160deg,#23b3ff,#0a7ef0)}
  .dock-apps{background:linear-gradient(160deg,#ff9a3a,#f56a22)}
</style>
</head>
<body>
<main class="app-window">
  <div class="window-dots"><span class="dot-yellow"></span><span class="dot-red"></span><span class="dot-green"></span></div>

  <div class="brand"><span class="brand-mark"></span>Hearthly</div>

  <div class="user-bar">
    <div class="theme-toggle">
      <svg width="13" height="13" viewBox="0 0 14 14"><circle cx="7" cy="7" r="3" fill="#ffd24a" stroke="#f5a000"/><g stroke="#f5a000" stroke-width="1.2" stroke-linecap="round"><path d="M7 .8v1.6M7 11.6v1.6M.8 7h1.6M11.6 7h1.6M2.6 2.6l1.1 1.1M10.3 10.3l1.1 1.1M2.6 11.4l1.1-1.1M10.3 3.7l1.1-1.1"/></g></svg>
      <span class="knob"></span>
    </div>
    <p class="welcome">Welcome, <b>Dara Whitlow</b></p>
    <div class="avatar" role="img" aria-label="User profile photo"></div>
  </div>

  <h1 class="section-title">
    <svg width="20" height="16" viewBox="0 0 20 16"><path d="M1 16V3h4V0h7v5h7v11z" fill="#1b2430"/><g fill="#fff"><rect x="3" y="6" width="2" height="2"/><rect x="7" y="3" width="2" height="2"/><rect x="7" y="7" width="2" height="2"/><rect x="3" y="10" width="2" height="2"/><rect x="7" y="11" width="2" height="2"/><rect x="14" y="8" width="2" height="2"/><rect x="14" y="12" width="2" height="2"/></g></svg>
    Properties list
  </h1>

  <nav class="property-tabs">
    <button>Prime tower</button><button>Prime tower</button><button>Prime tower</button><button>Prime tower</button><button>Prime tower</button><button>Prime tower</button><button>Prime tower</button>
  </nav>

  <div class="view-switch">
    <button class="btn-requests">
      <svg width="9" height="11" viewBox="0 0 9 11"><rect x=".5" y="1.5" width="8" height="9.5" rx="1" fill="#1b2430"/><rect x="2.5" y="0" width="4" height="2.5" rx=".6" fill="#1b2430"/><g stroke="#fff" stroke-width=".9"><path d="M2 5h5M2 7h5M2 9h5"/></g></svg>
      Request / orders
    </button>
    <button class="btn-calendar">
      <svg width="10" height="10" viewBox="0 0 10 10"><rect x="0" y="1.5" width="10" height="8.5" rx="1" fill="#fff"/><rect x="2" y="0" width="1.3" height="3" fill="#fff"/><rect x="6.7" y="0" width="1.3" height="3" fill="#fff"/><rect x="0" y="3.5" width="10" height="1" fill="#0d8ef5"/><rect x="2" y="6" width="2" height="2" fill="#0d8ef5"/></svg>
      Maintenance calendar
    </button>
  </div>

  <div class="month-nav">
    <h2>January 2021</h2>
    <span class="nav-btn nav-prev"><svg width="8" height="10" viewBox="0 0 8 10"><path d="M6 1L2 5l4 4" fill="none" stroke="#5d7a93" stroke-width="1.6" stroke-linecap="round" stroke-linejoin="round"/></svg></span>
    <span class="nav-btn nav-next"><svg width="8" height="10" viewBox="0 0 8 10"><path d="M2 1l4 4-4 4" fill="none" stroke="#1b2430" stroke-width="1.6" stroke-linecap="round" stroke-linejoin="round"/></svg></span>
  </div>

  <section class="calendar">
    <div class="weekdays"><span>Sunday</span><span>Monday</span><span>Tuesday</span><span>Wednesday</span><span>Thursday</span><span>Friday</span><span>Saturday</span></div>
    <div class="days">
      <div class="day past"><span class="day-num">27</span></div>
      <div class="day past"><span class="day-num">28</span></div>
      <div class="day past"><span class="day-num">29</span></div>
      <div class="day past"><span class="day-num">30</span></div>
      <div class="day past"><span class="day-num">31</span></div>
      <div class="day" style="padding-top:39px"><span class="day-num">01</span><div class="event blue">Maintenance Prime tower<br>6:00</div><div class="event orange">Maintenance Prime tower<br>6:00</div></div>
      <div class="day"><span class="day-num">02</span></div>

      <div class="day"><span class="day-num">03</span></div>
      <div class="day"><span class="day-num">04</span></div>
      <div class="day"><span class="day-num">05</span></div>
      <div class="day"><span class="day-num">06</span></div>
      <div class="day" style="padding-top:35px"><span class="day-num">07</span><div class="event blue">Maintenance Prime tower<br>6:00</div><div class="event orange">Maintenance Prime tower<br>6:00</div></div>
      <div class="day"><span class="day-num">08</span></div>
      <div class="day"><span class="day-num">09</span></div>

      <div class="day"><span class="day-num">10</span></div>
      <div class="day"><span class="day-num">11</span><div class="event blue">Maintenance Prime tower<br>6:00</div></div>
      <div class="day"><span class="day-num">12</span><div class="event blue">Maintenance Prime tower<br>6:00</div></div>
      <div class="day"><span class="day-num">13</span></div>
      <div class="day"><span class="day-num">14</span><div class="event blue">Maintenance Prime tower<br>6:00</div><div class="event orange">Maintenance Prime tower<br>6:00</div></div>
      <div class="day"><span class="day-num">15</span></div>
      <div class="day"><span class="day-num">16</span><div class="event blue">Maintenance Prime tower<br>6:00</div><div class="event orange">Maintenance Prime tower<br>6:00</div></div>

      <div class="day"><span class="day-num">17</span><div class="event blue">Maintenance Prime tower<br>6:00</div><div class="event orange">Maintenance Prime tower<br>6:00</div></div>
      <div class="day"><span class="day-num">18</span></div>
      <div class="day"><span class="day-num">19</span><div class="event blue">Maintenance Prime tower<br>6:00</div><div class="event orange">Maintenance Prime tower<br>6:00</div></div>
      <div class="day"><span class="day-num">20</span></div>
      <div class="day"><span class="day-num">21</span></div>
      <div class="day"><span class="day-num">22</span><div class="event blue">Maintenance Prime tower<br>6:00</div><div class="event orange">Maintenance Prime tower<br>6:00</div></div>
      <div class="day"><span class="day-num">23</span></div>
    </div>
  </section>

  <nav class="dock">
    <span class="dock-btn dock-home"><svg width="20" height="18" viewBox="0 0 20 18"><path d="M2 9L10 2l8 7" fill="none" stroke="#fff" stroke-width="2.2" stroke-linecap="round" stroke-linejoin="round"/><path d="M4.5 8v9h4v-5h3v5h4V8" fill="#fff"/></svg></span>
    <span class="dock-btn dock-apps"><svg width="16" height="16" viewBox="0 0 16 16" fill="#fff"><circle cx="3" cy="3" r="1.6"/><circle cx="8" cy="3" r="1.6"/><circle cx="13" cy="3" r="1.6"/><circle cx="3" cy="8" r="1.6"/><circle cx="8" cy="8" r="1.6"/><circle cx="13" cy="8" r="1.6"/><circle cx="3" cy="13" r="1.6"/><circle cx="8" cy="13" r="1.6"/><circle cx="13" cy="13" r="1.6"/></svg></span>
  </nav>
</main>
</body>
</html>
```